Business Card/ Email Signature Design Project

I am an Interior Designer. I need a business card that looks sophisticated stylish but simple in design. My work covers space design/ interior architecture/ furniture design/ product development & styling.

I have a very specific brief and know mostly what I want. I'm hoping to work with someone who can translate my ideas.

My branding should have a strong focus on my name, the majority of my work is referral based.
I'm keen to keep a monochromatic colour scheme: dark charcoal/ black/ white/ embossing/ silver. I'm not suggesting we use all that I've listed, they are possible ideas at this stage. I will need to be mindful of printing costs an also how I make the design work across, cards, letter heads, email logo and web design.

Theory behind images sent below;
1-Rug Image_(minus boarder) I was thinking this image could be used on the back of the card with my contact details over. I like that the lines are almost hand drawn and start to look free form. It's a subtle contrast to a more formal front of the card with my name.
2_Tomas Dreyer_I really like the orientation, the proportion of font on the card, the colour and the font. I like the lower case for my name and the upper case for 'Interior Design'. Not sure if it should be 'Interior Designer or Interior Design' at this stage, was leaning towards 'Interior Design'. Was thinking the 'i' and 'd' in my surname could be the colour eg 'silver'?? We can decide on this once we see it.

Look forward to hearing from you.
Cheers,
Noreen Balfour

Printing

Noreen Balfour Interior Design

```html
<!DOCTYPE html>
<html lang="en">
<head>
<meta charset="utf-8">
<title>Noreen Balfour Interior Design — Business Card</title>
<link rel="stylesheet" href="https://fonts.googleapis.com/css2?family=Inter:wght@400;700&display=swap">
<style>
  :root {
    --backdrop: #e9e6e1;
    --card-black: #0c0c0c;
    --name-white: #ffffff;
    --tagline-grey: #5e5e5e;
    --rug-light: #e4e2dd;
    --rug-mid: #cfccc6;
    --ink-dark: #1a1a1a;
    --back-tagline: #555555;
  }
  * { margin: 0; padding: 0; box-sizing: border-box; }
  html, body {
    width: 1200px;
    height: 1000px;
    overflow: hidden;
    background: var(--backdrop);
    font-family: "Inter", "Helvetica Neue", Arial, sans-serif;
  }
  .canvas {
    position: relative;
    width: 1200px;
    height: 1000px;
  }
  .card {
    position: absolute;
    width: 730px;
    height: 416px;
    box-shadow: 0 6px 18px rgba(0, 0, 0, 0.25);
  }

  /* Front of card: name on black (sits underneath) */
  .card-front {
    left: 26px;
    top: 463px;
    height: 417px;
    background: var(--card-black);
    z-index: 1;
  }
  .front-brand {
    position: absolute;
    left: 134px;
    top: 160px;
  }
  .front-brand .name {
    font-weight: 700;
    font-size: 60px;
    line-height: 1;
    color: var(--name-white);
  }
  .front-brand .tagline {
    font-weight: 400;
    font-size: 34px;
    line-height: 1;
    margin-top: 10px;
    color: var(--tagline-grey);
  }

  /* Back of card: rug texture with contact details (on top) */
  .card-back {
    left: 378px;
    top: 120px;
    overflow: hidden;
    z-index: 2;
  }
  .rug-texture {
    position: absolute;
    inset: 0;
    background: radial-gradient(ellipse at 40% 45%, var(--rug-light) 0%, var(--rug-mid) 100%);
  }
  .back-brand {
    position: absolute;
    right: 28px;
    top: 50px;
  }
  .back-brand .name {
    font-weight: 700;
    font-size: 27px;
    line-height: 1;
    color: var(--name-white);
  }
  .back-brand .tagline {
    font-weight: 400;
    font-size: 17px;
    line-height: 1;
    margin-top: 6px;
    color: var(--back-tagline);
  }
  .contact {
    position: absolute;
    left: 26px;
    top: 262px;
    list-style: none;
  }
  .contact li {
    font-weight: 700;
    font-size: 14px;
    line-height: 25.5px;
    color: var(--ink-dark);
    letter-spacing: 2.4px;
  }
</style>
</head>
<body>
<div class="canvas">

  <section class="card card-front" aria-label="Card front">
    <div class="front-brand">
      <div class="name">noreen balfour</div>
      <div class="tagline">Interior Design</div>
    </div>
  </section>

  <section class="card card-back" aria-label="Card back">
    <div class="rug-texture" role="img" aria-label="Photograph of a pale woven rug with loose hand-drawn dark lattice lines"></div>
    <div class="back-brand">
      <div class="name">noreen balfour</div>
      <div class="tagline">Interior Design</div>
    </div>
    <ul class="contact">
      <li>0400 555 019</li>
      <li>www.noreenbalfour.com</li>
      <li>interiors@noreenbalfour.com</li>
      <li>P.O Box 482 Elmsford VIC. 3999</li>
    </ul>
  </section>

</div>
</body>
</html>
```